BrivoNest Learning App for Children with Dyslexia

Project Description:

We are seeking a talented UI/UX designer to create engaging and intuitive designs for Brivonest, an innovative educational app designed to help children learn letters and words through a multisensory learning approach. The app aims to be particularly helpful for children with dyslexia, providing a supportive and interactive learning environment.

Key App Features & Design Requirements:

Account Creation Screen: Design a welcoming and straightforward sign-up page that allows users to register with their email or continue with Quarnix. The design should be clean, focusing on user-friendliness and accessibility, adhering to our terms of service and privacy policy.

Main Screen Design: The main screen should allocate at least 4/6 of its height to the interactive drawing area. It needs to display word prompts in both correct and scrambled orders and include options to "Show all Words," "Play all words," and a search function. The interface should be vibrant, engaging, and easy to navigate for children.

Profile Section: Create a user-friendly profile page that allows users to edit their profile image, name, username, email, links, and bio. The design should be clean and encourage user engagement.

BrivoTally Page: This section will display the user's learning progress, including rankings, a learning curve, and recently learned words. It should visually represent progress in a motivating and understandable way, suitable for a younger audience.

Visual and Auditory Feedback Implementation: Incorporate elements that support visual and auditory feedback, using dyslexia-friendly formats. This includes choosing appropriate colors, fonts, and auditory cues.

Accessibility and Customization Settings: Designs should include settings for adjusting visual contrast, font size, and the word list to accommodate individual preferences and needs.

Feel free to add more interactions and/or pages.

Design preferences:

Color Scheme: Use a bright, inviting color palette that stimulates learning and engagement without overwhelming the users.
Font Selection: Opt for fonts that are readable and accessible, particularly for users with dyslexia.
Icons and Graphics: Design custom icons and graphics that are cohesive with the app's theme and purpose. Illustrations should be simple, relatable, and supportive of the learning process.

Target Market(s)

Educational

Industry/Entity Type

Educational

Colors
0054AA
0677BA
7BADD7
CADEEF
E8F1F8
0094D4
00A9DD
6FCCEA
C7EBF8
E9F6FB

Requirements
Must have
• Educational app, a writing area, scoring and account management
Nice to have
• Statistics, Ranking Page, Settings and some nice visual features

```html
<!DOCTYPE html>
<html lang="en">
<head>
<meta charset="utf-8">
<title>Brivonest – App Screens</title>
<link href="https://fonts.googleapis.com/css2?family=Lexend:wght@400;500;600;700&display=swap" rel="stylesheet">
<style>
  :root{
    --navy:#0054AA;
    --sky:#00A9DD;
    --ocean:#0094D4;
    --pale:#E9F6FB;
    --ink:#111418;
    --muted:#6b7076;
    --field:#EEEEEE;
    --surface:#FFFFFF;
    --draw:#F2F2F2;
    --stage:#E8F1F8;
  }
  *{box-sizing:border-box;margin:0;padding:0}
  html,body{width:1200px;height:782px;overflow:hidden}
  body{background:var(--stage);font-family:"Lexend",sans-serif;color:var(--ink);position:relative}
  .screen{position:absolute;top:101px;width:284px;height:611px;background:var(--surface);border-radius:32px;overflow:hidden;box-shadow:0 6px 24px rgba(0,60,120,.10)}
  .screen--signup{left:80px}
  .screen--main{left:458px}
  .screen--profile{left:828px}
  .abs{position:absolute}
  .center-x{left:0;right:0;text-align:center}
  .status{top:20px;left:0;right:0;height:16px;display:flex;justify-content:space-between;align-items:center;padding:0 4px 0 4px;font-size:13px;font-weight:500}
  .status__icons{display:flex;gap:4px;align-items:center}

  /* sign up */
  .brand{top:52px;font-size:27px;font-weight:700}
  .tagline{top:88px;font-size:11px}
  .hero-art{left:50px;top:120px;width:182px;height:126px;border-radius:40px;background:linear-gradient(135deg,#C7EBF8,#CADEEF 60%,#E9F6FB)}
  .heading{top:270px;font-size:20px;font-weight:600}
  .sub{top:301px;font-size:11px;font-weight:500}
  .field{left:13px;width:260px;top:331px;height:35px;background:var(--field);border-radius:7px;font-size:11.5px;padding-left:16px;display:flex;align-items:center}
  .btn-primary{left:13px;width:260px;top:377px;height:35px;background:var(--navy);color:#fff;border-radius:7px;font-size:11.5px;font-weight:600;display:flex;align-items:center;justify-content:center}
  .divider-text{top:432px;font-size:11px;font-weight:500}
  .btn-alt{left:13px;width:260px;top:466px;height:36px;background:var(--field);border-radius:7px;font-size:12px;font-weight:500;display:flex;align-items:center;justify-content:center;gap:8px}
  .btn-alt__dot{width:12px;height:12px;border-radius:50%;background:var(--ocean)}
  .legal{top:516px;font-size:8px;line-height:15px}
  .legal a{color:var(--ocean);text-decoration:none}
  .pager{top:570px;display:flex;justify-content:center;gap:5px}
  .pager span{width:6px;height:6px;border-radius:50%;background:var(--ocean)}
  .pager span.off{background:#cfd6db}

  /* main */
  .menu{left:12px;top:41px}
  .title{top:37px;font-size:21px;font-weight:600}
  .points{right:0;top:43px;font-size:11px;font-weight:600}
  .side-wave{right:0;top:62px}
  .canvas-area{left:29px;top:87px;width:234px;height:226px;border:1.5px dashed #222;border-radius:8px;padding:6px}
  .canvas-area__pad{width:100%;height:100%;background:var(--draw);border-radius:6px;display:flex;align-items:center;justify-content:center}
  .toggle{left:39px;top:344px;width:213px;height:35px;background:#fff;border-radius:18px;box-shadow:0 2px 10px rgba(0,0,0,.06);display:flex;font-size:9.5px;font-weight:600}
  .toggle__opt{flex:1;display:flex;align-items:center;justify-content:center;border-radius:18px}
  .toggle__opt--on{background:var(--sky);color:#fff;flex:1.15}
  .chip{height:31px;width:75px;background:#fff;border-radius:16px;box-shadow:0 2px 10px rgba(0,0,0,.07);font-size:10.5px;font-weight:600;display:flex;align-items:center;justify-content:center}
  .bottom-wave{left:0;bottom:0}
  .btn-results{left:79px;top:512px;width:135px;height:34px;background:var(--navy);color:#fff;border-radius:17px;font-size:9.5px;font-weight:600;display:flex;align-items:center;justify-content:center}

  /* profile */
  .back{left:16px;top:57px}
  .page-title{top:56px;font-size:20px;font-weight:600}
  .avatar{left:105px;top:113px;width:72px;height:72px;border-radius:50%;background:linear-gradient(135deg,#4a4f45,#2d2a26)}
  .edit-link{top:199px;font-size:12.5px;font-weight:600;color:var(--navy)}
  .row{left:20px;width:248px;background:#fff;border-radius:12px;box-shadow:0 2px 12px rgba(0,0,0,.07);font-size:10px}
  .row__label{position:absolute;left:17px;top:13px;font-weight:600;font-size:11px}
  .row__value{position:absolute;left:90px;top:14px;line-height:16px}
  .row__value .add{color:var(--muted)}
  .row__chev{position:absolute;right:12px;top:15px}
</style>
</head>
<body>

<!-- Sign up screen -->
<section class="screen screen--signup">
  <div class="abs status"><span>9:41</span>
    <span class="status__icons">
      <svg width="16" height="10" viewBox="0 0 16 10"><rect x="0" y="7" width="3" height="3" fill="#111"/><rect x="4" y="5" width="3" height="5" fill="#111"/><rect x="8" y="3" width="3" height="7" fill="#111"/><rect x="12" y="0" width="3" height="10" fill="#111"/></svg>
      <svg width="14" height="10" viewBox="0 0 14 10"><path d="M7 10 L4.5 7 A4 4 0 0 1 9.5 7 Z M1 4 A9 9 0 0 1 13 4 L11.5 5.5 A7 7 0 0 0 2.5 5.5Z" fill="#111"/></svg>
      <svg width="22" height="10" viewBox="0 0 22 10"><rect x="0" y="0" width="20" height="10" rx="2.5" fill="#111"/><rect x="20.5" y="3" width="1.5" height="4" fill="#111"/></svg>
    </span></div>
  <div class="abs center-x brand">Brivonest</div>
  <div class="abs center-x tagline">Learn letters and words</div>
  <div class="abs hero-art" role="img" aria-label="Illustration of two children playing with colourful letters, gears and a light bulb"></div>
  <div class="abs center-x heading">Create an account</div>
  <div class="abs center-x sub">Enter your email to sign up for this app</div>
  <div class="abs field">email@mailbox.web</div>
  <div class="abs btn-primary">Sign Up With Email</div>
  <div class="abs center-x divider-text">or continue with</div>
  <div class="abs btn-alt"><span class="btn-alt__dot"></span>Quarnix</div>
  <p class="abs center-x legal">By clicking continue, you agree to our <a href="#">Terms of Service</a><br>and <a href="#">Privacy Policy</a></p>
  <div class="abs center-x pager"><span></span><span class="off"></span><span></span></div>
</section>

<!-- Main screen -->
<section class="screen screen--main">
  <div class="abs status" style="top:12px;padding:0 6px"><span>9:41</span>
    <span class="status__icons">
      <svg width="16" height="10" viewBox="0 0 16 10"><rect x="0" y="7" width="3" height="3" fill="#111"/><rect x="4" y="5" width="3" height="5" fill="#111"/><rect x="8" y="3" width="3" height="7" fill="#111"/><rect x="12" y="0" width="3" height="10" fill="#111"/></svg>
      <svg width="14" height="10" viewBox="0 0 14 10"><path d="M7 10 L4.5 7 A4 4 0 0 1 9.5 7 Z M1 4 A9 9 0 0 1 13 4 L11.5 5.5 A7 7 0 0 0 2.5 5.5Z" fill="#111"/></svg>
      <svg width="22" height="10" viewBox="0 0 22 10"><rect x="0" y="0" width="20" height="10" rx="2.5" fill="#111"/></svg>
    </span></div>
  <svg class="abs side-wave" width="30" height="225" viewBox="0 0 30 225"><path d="M30 0 C12 12 0 40 0 90 L0 160 C4 190 18 210 30 225 Z" fill="var(--navy)"/></svg>
  <svg class="abs menu" width="15" height="13" viewBox="0 0 15 13"><g fill="#111"><rect y="0" width="15" height="2"/><rect y="4" width="15" height="2"/><rect y="8" width="15" height="2"/><rect y="12" width="15" height="1.5"/></g></svg>
  <div class="abs center-x title">Main Screen</div>
  <div class="abs points">16 Points</div>
  <div class="abs canvas-area"><div class="canvas-area__pad">
    <svg width="42" height="42" viewBox="0 0 42 42"><path d="M30 3 L39 12 L14 37 L3 39 L5 28 Z" fill="#9a9a9a"/><path d="M25 8 L34 17" stroke="#F2F2F2" stroke-width="2.5"/><path d="M7 31 L11 35" stroke="#F2F2F2" stroke-width="2"/></svg>
  </div></div>
  <div class="abs toggle"><span class="toggle__opt">Show all Words</span><span class="toggle__opt toggle__opt--on">Play all words</span></div>
  <svg class="abs bottom-wave" width="284" height="180" viewBox="0 0 284 180"><path d="M0 0 C14 20 20 70 38 110 C60 150 120 150 190 158 C215 161 240 168 255 180 L0 180 Z" fill="var(--sky)"/></svg>
  <div class="abs chip" style="left:21px;top:411px">Word 1</div>
  <div class="abs chip" style="left:109px;top:411px">Word 2</div>
  <div class="abs chip" style="left:197px;top:411px">Word 3</div>
  <div class="abs chip" style="left:65px;top:453px">Word 4</div>
  <div class="abs chip" style="left:152px;top:453px">...</div>
  <div class="abs btn-results">Show me the results</div>
</section>

<!-- Profile screen -->
<section class="screen screen--profile">
  <div class="abs status" style="padding:0 6px 0 8px"><span>9:41</span>
    <span class="status__icons">
      <svg width="16" height="10" viewBox="0 0 16 10"><rect x="0" y="7" width="3" height="3" fill="#111"/><rect x="4" y="5" width="3" height="5" fill="#111"/><rect x="8" y="3" width="3" height="7" fill="#111"/><rect x="12" y="0" width="3" height="10" fill="#111"/></svg>
      <svg width="14" height="10" viewBox="0 0 14 10"><path d="M7 10 L4.5 7 A4 4 0 0 1 9.5 7 Z M1 4 A9 9 0 0 1 13 4 L11.5 5.5 A7 7 0 0 0 2.5 5.5Z" fill="#111"/></svg>
      <svg width="22" height="10" viewBox="0 0 22 10"><rect x="0" y="0" width="20" height="10" rx="2.5" fill="#111"/><rect x="20.5" y="3" width="1.5" height="4" fill="#111"/></svg>
    </span></div>
  <svg class="abs back" width="10" height="14" viewBox="0 0 10 14"><path d="M8 1 L2 7 L8 13" stroke="#111" stroke-width="2" fill="none"/></svg>
  <div class="abs center-x page-title">Profile</div>
  <div class="abs avatar" role="img" aria-label="Profile photo of the user"></div>
  <div class="abs center-x edit-link">Edit profile image</div>

  <div class="abs row" style="top:241px;height:33px"><span class="row__label">Name</span><span class="row__value">Marla Quent</span><svg class="row__chev" width="6" height="8" viewBox="0 0 6 8"><path d="M1 1 L4 4 L1 7" stroke="#111" stroke-width="1.3" fill="none"/></svg></div>
  <div class="abs row" style="top:286px;height:33px"><span class="row__label">Username</span><span class="row__value">@username</span><svg class="row__chev" width="6" height="8" viewBox="0 0 6 8"><path d="M1 1 L4 4 L1 7" stroke="#111" stroke-width="1.3" fill="none"/></svg></div>
  <div class="abs row" style="top:333px;height:33px"><span class="row__label">Email</span><span class="row__value">name@mailbox.web</span><svg class="row__chev" width="6" height="8" viewBox="0 0 6 8"><path d="M1 1 L4 4 L1 7" stroke="#111" stroke-width="1.3" fill="none"/></svg></div>
  <div class="abs row" style="top:378px;height:79px"><span class="row__label">Links</span><span class="row__value" style="top:10px">homepage.web<br>linkplace.web<br>yourpage.web<br><span class="add">+ Add link</span></span><svg class="row__chev" width="6" height="8" viewBox="0 0 6 8"><path d="M1 1 L4 4 L1 7" stroke="#111" stroke-width="1.3" fill="none"/></svg></div>
  <div class="abs row" style="top:473px;height:33px"><span class="row__label">Bio</span><span class="row__value" style="left:87px">A description of this user.</span><svg class="row__chev" width="6" height="8" viewBox="0 0 6 8"><path d="M1 1 L4 4 L1 7" stroke="#111" stroke-width="1.3" fill="none"/></svg></div>
</section>

</body>
</html>
```